Brightway Haus Inc. Business Card Design

Brightway Haus Inc. is in search of a great clean design for our business cards!

Looking to incorporate our full logo and watermark on side one (however, I am open to having the text and watermark separated within the design.)

On side two, I am looking to have contact information (Name, Position, Phone #, Email, Website (www.thebrightwayhaus.ca). Can have the logo and/or watermark as part of the design if applicable.

Please add tagline "Where Shine Counts" on either side 1 or 2. This tagline can be in a sans serif, serif or cursive font as long as it compliments overall design. Capitalization can be title or sentence case depending on how it fits within the design.

Get creative!! Looking for a clean, crisp, premium design! Looking for a glossy card finish with spot UV features when printed. Cards will also be printed with rounded corners. Standard dimensions (3.5 x 2).

Target Market(s)

B2B - primary clients are business owners or property management corporations. (residential jobs are few and far between)

Industry/Entity Type

Business

Contact Information for Business Card

- clean, crisp design
- double sided
- spot UV accents and glossy finish upon printing
- standard business card size (3.5 x 2) with rounded corners
- please see project description for requirements per side

Font styles to use
Sans Serif

Requirements
Must have
• - adequate bleeds with print ready files
• - cohesive design elements between side 1 & 2
• - spot UV elements (can be on both sides or just one, use your discretion)
• - colour pallet should match the logo file provided
• - incorporate tagline "where shine counts" (this tagline can be in a serif or sans serif font as long as it is complimentary to the overall design.
Nice to have
• - Premium elements with a clean design
Should not have
• - Please omit cartoon or whimsical like designs, think premium.
• - Colours should not stray from the pallet of the provided logo.

```html
<!DOCTYPE html>
<html lang="en">
<head>
<meta charset="utf-8">
<title>Brightway Haus Inc. Business Card</title>
<link rel="stylesheet" href="https://fonts.googleapis.com/css2?family=Montserrat:wght@500;700;800&family=Work+Sans:wght@400;500&display=swap">
<style>
  :root {
    --navy: #1c2660;
    --navy-light: #253274;
    --teal: #17b3b3;
    --white: #ffffff;
    --ink: #1c2660;
    --stage: #4a4a4c;
    --rule: #2a3468;
  }
  * { box-sizing: border-box; margin: 0; padding: 0; }
  html, body { width: 1200px; height: 859px; overflow: hidden; }
  body {
    background: var(--stage);
    position: relative;
    font-family: "Work Sans", Arial, sans-serif;
  }
  .card {
    position: absolute;
    width: 560px;
    height: 320px;
    border-radius: 10px;
    overflow: hidden;
    box-shadow: 0 10px 24px rgba(0,0,0,.35);
  }

  /* Side one */
  .card-front {
    left: 70px; top: 70px;
    background: var(--navy);
  }
  .front-map {
    position: absolute;
    left: 60px; top: 30px;
    width: 440px; height: 250px;
    border-radius: 40px;
    background: radial-gradient(ellipse at center, var(--navy-light) 0%, rgba(37,50,116,0) 70%);
  }
  .front-brand {
    position: absolute;
    left: 0; right: 0; top: 118px;
    display: flex; align-items: center; justify-content: center; gap: 12px;
  }
  .brand-mark {
    width: 30px; height: 30px;
    background: var(--teal);
  }
  .brand-name {
    font-family: "Montserrat", Arial, sans-serif;
    font-weight: 800;
    font-size: 34px;
    letter-spacing: -0.5px;
    text-transform: uppercase;
  }
  .front-brand .brand-name { color: var(--white); }
  .front-tagline {
    position: absolute;
    left: 0; right: 0; top: 245px;
    text-align: center;
    color: var(--white);
    font-family: "Montserrat", Arial, sans-serif;
    font-weight: 500;
    font-size: 14px;
    letter-spacing: 4px;
    text-transform: uppercase;
  }

  /* Side two */
  .card-back {
    left: 570px; top: 469px;
    background: var(--white);
  }
  .back-brand {
    position: absolute;
    right: 30px; top: 34px;
    display: flex; align-items: center; gap: 8px;
  }
  .back-brand .brand-mark { width: 20px; height: 20px; }
  .back-brand .brand-name { font-size: 22px; color: var(--teal); }
  .rule {
    position: absolute;
    left: 34px; right: 34px;
    height: 1px;
    background: var(--rule);
  }
  .rule-top { top: 140px; }
  .rule-mid { top: 222px; }
  .person {
    position: absolute;
    left: 34px; top: 172px;
  }
  .person-name {
    font-family: "Montserrat", Arial, sans-serif;
    font-weight: 700;
    font-size: 24px;
    color: var(--ink);
    line-height: 1;
    text-transform: uppercase;
  }
  .person-role {
    font-family: "Montserrat", Arial, sans-serif;
    font-weight: 700;
    font-size: 11px;
    letter-spacing: .5px;
    color: var(--teal);
    text-transform: uppercase;
    margin-top: 4px;
  }
  .contact {
    position: absolute;
    left: 34px; top: 234px;
    font-size: 10.5px;
    line-height: 20px;
    color: var(--ink);
  }
  .contact .label { font-weight: 500; margin-right: 4px; }
  .contact .value { color: var(--teal); margin-right: 8px; }
  .contact .value strong { color: var(--ink); font-weight: 500; }
  .back-band {
    position: absolute;
    left: 0; bottom: 0;
    width: 560px; height: 42px;
    display: block;
  }
</style>
</head>
<body>

  <section class="card card-front" aria-label="Business card, side one">
    <div class="front-map" role="img" aria-label="Faint dotted world map watermark"></div>
    <div class="front-brand">
      <span class="brand-mark"></span>
      <span class="brand-name">Brightway Haus Inc.</span>
    </div>
    <p class="front-tagline">Where Shine Counts</p>
  </section>

  <section class="card card-back" aria-label="Business card, side two">
    <div class="back-brand">
      <span class="brand-mark"></span>
      <span class="brand-name">Brightway Haus Inc.</span>
    </div>
    <div class="rule rule-top"></div>
    <div class="person">
      <p class="person-name">Marcus Hale</p>
      <p class="person-role">Director</p>
    </div>
    <div class="rule rule-mid"></div>
    <div class="contact">
      <p>
        <span class="label">P :</span><span class="value">555-014-2290</span>
        <span class="label">E :</span><span class="value">info@brightwayhaus-services.ca</span>
        <span class="label">W :</span><span class="value">www.<strong>thebrightwayhaus</strong>.ca</span>
      </p>
      <p>
        <span class="label">A :</span><span class="value">418 Harbour Road Suite 210 Lakeview ON L0R 2K4.</span>
      </p>
    </div>
    <svg class="back-band" viewBox="0 0 560 42" preserveAspectRatio="none" aria-hidden="true">
      <polygon points="0,32 560,6 560,42 0,42" fill="var(--navy)"/>
      <polygon points="300,22 560,0 560,12 330,24" fill="var(--teal)"/>
    </svg>
  </section>

</body>
</html>
```